Varnex Consulting Business card design.

See our website www.varnexconsulting.example which will give you a good idea of what we are about. The font is called 'Play'.

I'd like a standout business card in keeping with the themes and branding on the website

Target Market(s)

professionals. HR directors

Industry/Entity Type

Business

Contact Information for Business Card

Varnex Consulting PO Box 3172 Merrowdale NSW 2291 1300 485 193 Gavin Threlkeld Principal email: career@varnexconsulting.example ABN: 71203948865

Font styles to use
Other font styles liked:
• Play

Requirements
Must have
• Must have same design colours and branding as website.
• On back I'd prefer a list of the things we do which appears below the name at the header on the website

```html
<!DOCTYPE html>
<html lang="en">
<head>
<meta charset="utf-8">
<title>Varnex Consulting – Business Card</title>
<link rel="stylesheet" href="https://fonts.googleapis.com/css2?family=Play:wght@400;700&display=swap">
<style>
  :root {
    --navy: #11293e;
    --blue: #2196e0;
    --white: #ffffff;
    --paper: #f7f8f8;
    --backdrop: #a6a3a4;
  }
  * { margin: 0; padding: 0; box-sizing: border-box; }
  html, body { width: 1200px; height: 1200px; overflow: hidden; }
  body {
    background: var(--backdrop);
    font-family: 'Play', sans-serif;
    position: relative;
  }
  .card {
    position: absolute;
    left: 244px;
    width: 712px;
    height: 418px;
    overflow: hidden;
  }
  .card--front { top: 118px; background: var(--navy); }
  .card--back  { top: 664px; background: var(--paper); }

  .wordmark {
    position: absolute;
    left: 0; right: 0;
    text-align: center;
    font-weight: 400;
    letter-spacing: 1px;
    line-height: 1;
    white-space: nowrap;
  }
  .card--front .wordmark { top: 128px; font-size: 58px; color: var(--white); }
  .card--back  .wordmark { top: 64px;  font-size: 62px; color: var(--navy); }

  .services {
    position: absolute;
    left: 0; right: 0;
    text-align: center;
    color: var(--blue);
    font-size: 15px;
    letter-spacing: 3.2px;
    white-space: nowrap;
  }
  .card--front .services { top: 191px; }
  .card--back  .services { top: 126px; letter-spacing: 3.6px; }
  .services .sep { margin: 0 2px; }

  .front-url {
    position: absolute;
    top: 350px; left: 0; right: 0;
    display: flex;
    justify-content: center;
    align-items: center;
    gap: 12px;
    color: var(--white);
    font-size: 17px;
    letter-spacing: 0.5px;
  }
  .accent { color: var(--blue); }
  .dash { display: block; }

  .person {
    position: absolute;
    left: 41px; top: 211px;
    color: var(--navy);
  }
  .person__name { font-size: 23px; font-weight: 700; line-height: 1; }
  .person__role { font-size: 17px; margin-top: 12px; }

  .contact {
    position: absolute;
    left: 332px; top: 216px;
    color: var(--navy);
    font-size: 18px;
    line-height: 1;
  }
  .contact__row { display: flex; align-items: center; height: 27px; }
  .contact__icon { width: 36px; display: flex; align-items: center; }
  .contact__line { height: 31px; display: flex; align-items: center; letter-spacing: 0.3px; }
  .contact__row + .contact__line { margin-top: 4px; }

  .base-band { position: absolute; left: 0; bottom: 0; display: block; }
</style>
</head>
<body>

  <section class="card card--front" aria-label="Business card front">
    <h1 class="wordmark">VARNEX CONSULTING</h1>
    <p class="services">Search &amp; Select <span class="sep">|</span> Career <span class="sep">|</span> Coaching <span class="sep">|</span> Leadership <span class="sep">|</span> Outplacement</p>
    <div class="front-url">
      <svg class="dash" width="36" height="4" viewBox="0 0 36 4"><path d="M0 2 L36 0.5 L36 3.5 Z" fill="var(--blue)"/></svg>
      <span>www.<span class="accent">varnexconsulting</span>.example</span>
      <svg class="dash" width="36" height="4" viewBox="0 0 36 4"><path d="M36 2 L0 0.5 L0 3.5 Z" fill="var(--blue)"/></svg>
    </div>
  </section>

  <section class="card card--back" aria-label="Business card back">
    <h2 class="wordmark">VARNEX CONSULTING</h2>
    <p class="services">Search &amp; Select <span class="sep">|</span> Career <span class="sep">|</span> Coaching <span class="sep">|</span> Leadership <span class="sep">|</span> Outplacement</p>

    <div class="person">
      <p class="person__name">Gavin Threlkeld</p>
      <p class="person__role">Principal</p>
    </div>

    <div class="contact">
      <div class="contact__row">
        <span class="contact__icon">
          <svg width="18" height="14" viewBox="0 0 18 14" aria-hidden="true"><path d="M1 5 Q9 -1 17 5 L14 7 L12 4 L6 4 L4 7 Z" fill="var(--blue)"/><rect x="4" y="7" width="10" height="6" rx="1" fill="var(--blue)"/></svg>
        </span>
        <span>1300 485 193</span>
      </div>
      <div class="contact__row">
        <span class="contact__icon">
          <svg width="16" height="16" viewBox="0 0 16 16" aria-hidden="true"><g fill="none" stroke="var(--blue)" stroke-width="1.4"><circle cx="8" cy="8" r="7"/><ellipse cx="8" cy="8" rx="3" ry="7"/><path d="M1 8h14M2.5 4.5h11M2.5 11.5h11"/></g></svg>
        </span>
        <span>www.<span class="accent">varnexconsulting</span>.example</span>
      </div>
      <div class="contact__row">
        <span class="contact__icon">
          <svg width="18" height="13" viewBox="0 0 18 13" aria-hidden="true"><rect x="0.7" y="0.7" width="16.6" height="11.6" fill="none" stroke="var(--blue)" stroke-width="1.4"/><path d="M1 1 L9 7.5 L17 1 M1 12 L7 6 M17 12 L11 6" fill="none" stroke="var(--blue)" stroke-width="1.4"/></svg>
        </span>
        <span>career@varnexconsulting.example</span>
      </div>
      <p class="contact__line"><span class="accent">ABN:</span>&nbsp;71203948865</p>
      <p class="contact__line">PO Box 3172 Merrowdale NSW 2291</p>
    </div>

    <svg class="base-band" width="712" height="20" viewBox="0 0 712 20" aria-hidden="true">
      <polygon points="0,2 500,2 464,20 0,20" fill="var(--navy)"/>
      <polygon points="506,2 712,2 712,20 472,20" fill="var(--blue)"/>
    </svg>
  </section>

</body>
</html>
```